Buch-/eBook-Cover für Traumatherapeutin
Zielgruppe
Ich bin Traumatherapeutin und schreibe ein Buch zum Thema Trauma bearbeiten.
Meine Zielgruppe sucht Heilung, Genesung, Selbstliebe etc.
Aufgabenstellung
Buchcover
Bitte erstell mir ein modernes positives inspirierendes Buchcover mit dem
Titel: 'Morgenlicht NEU entdecken“
Untertitel: „Spüre den Mut der ganz in dir wohnt“
Dr. Mira Kessow
Ich hätte gerne ein modernes Buch, das entweder einen Bezug zum Thema Trauma hat oder aber einfach stylische Schriftzüge. Bin aber auch offen für andere Vorschläge.
Dunkelblau, weiß und türkis oder auch rosa mag ich ganz gerne. Wobei Dunkelblau, weiß und türkis meine Favoriten sind und mit rosa höchstens kleinere Akzente gesetzt werden sollten.
Das Buchcover soll modern sein und direkt ansprechen. Gerne eine originelle Lösung, oder etwas Besonderes, etwas das Tiefe ausdrückt, oder man mehrmals hinsehen muss um etwas zu erkennen oder etwas das mehr Interpretationsspielraum lässt.
Gerne auch viel weiß, zumindest heller und nicht zu dunkel. Stylish, aber nicht überfrachtet.
Schreib mich gerne an, wenn du Fragen hast.
Ich habe mal zwei Beispiel von Typolösungen angehängt, die ich ganz cool fände.
Ich freue mich auf deine Ideen :-)
Ganz liebe Grüße
Mira

```html
<!DOCTYPE html>
<html lang="de">
<head>
<meta charset="utf-8">
<title>Morgenlicht neu entdecken – Dr. Mira Kessow</title>
<link href="https://fonts.googleapis.com/css2?family=Source+Sans+3:wght@400;700&family=Great+Vibes&display=swap" rel="stylesheet">
<style>
  :root {
    --teal: #208ca9;
    --navy: #3f68a2;
    --aqua-soft: #5aa3b4;
    --mist-light: #e8ecf1;
    --mist-mid: #c9dce8;
    --ice-blue: #9fc1da;
    --aqua-wash: #b3e0ea;
  }
  html, body {
    margin: 0;
    padding: 0;
    overflow: hidden;
    background: #ffffff;
  }
  .cover {
    position: relative;
    width: 846px;
    height: 1200px;
    overflow: hidden;
    font-family: "Source Sans 3", sans-serif;
    background: var(--mist-light);
  }
  .watercolour {
    position: absolute;
    inset: 0;
  }
  .author-band {
    position: absolute;
    left: 0;
    top: 127px;
    width: 100%;
    height: 54px;
    background: linear-gradient(90deg, rgba(255,255,255,0.85), rgba(255,255,255,0.6) 65%, rgba(225,238,246,0.55));
    display: flex;
    align-items: center;
    justify-content: center;
  }
  .author {
    margin: 0;
    font-weight: 700;
    font-size: 38px;
    letter-spacing: 1px;
    color: var(--navy);
    line-height: 1;
  }
  .title {
    margin: 0;
    font-weight: 700;
  }
  .title-line,
  .title-script {
    position: absolute;
    left: 0;
    width: 100%;
    text-align: center;
    line-height: 1;
    white-space: nowrap;
  }
  .title-line {
    color: var(--teal);
    text-transform: uppercase;
  }
  .title-line--first {
    top: 312px;
    font-size: 116px;
  }
  .title-script {
    top: 436px;
    font-family: "Great Vibes", cursive;
    font-weight: 400;
    font-size: 175px;
    color: var(--navy);
  }
  .title-line--last {
    top: 603px;
    font-size: 122px;
  }
  .wave {
    position: absolute;
    left: 0;
    top: 750px;
    width: 846px;
    height: 100px;
  }
  .subtitle-band {
    position: absolute;
    left: 0;
    top: 895px;
    width: 100%;
    height: 133px;
    background: linear-gradient(90deg, rgba(255,255,255,0.78), rgba(255,255,255,0.66) 60%, rgba(236,243,248,0.7));
  }
  .subtitle {
    position: absolute;
    inset: 0;
    margin: 0;
    font-weight: 400;
    color: var(--aqua-soft);
    font-size: 40px;
    line-height: 1;
  }
  .subtitle-line {
    position: absolute;
    white-space: nowrap;
  }
  .subtitle-line--first {
    left: 160px;
    top: 41px;
  }
  .subtitle-script {
    font-family: "Great Vibes", cursive;
    font-size: 76px;
    line-height: 0;
  }
  .subtitle-line--second {
    right: 160px;
    top: 83px;
  }
</style>
</head>
<body>
  <main class="cover">
    <svg class="watercolour" width="846" height="1200" viewBox="0 0 846 1200" role="img" aria-label="Aquarell-Hintergrund in Eisblau, Weiß und Türkis">
      <defs>
        <filter id="soft-blur" x="-30%" y="-30%" width="160%" height="160%">
          <feGaussianBlur stdDeviation="45"/>
        </filter>
        <filter id="grain">
          <feTurbulence type="fractalNoise" baseFrequency="0.9" numOctaves="2" seed="4"/>
          <feColorMatrix type="matrix" values="0 0 0 0 1  0 0 0 0 1  0 0 0 0 1  0 0 0 0.55 -0.18"/>
        </filter>
        <linearGradient id="base-wash" x1="0" y1="0" x2="1" y2="1">
          <stop offset="0" stop-color="#d3e7ef"/>
          <stop offset="0.35" stop-color="#e7ecf1"/>
          <stop offset="0.65" stop-color="#e3e9ef"/>
          <stop offset="1" stop-color="#b6d0e2"/>
        </linearGradient>
      </defs>
      <rect width="846" height="1200" fill="url(#base-wash)"/>
      <g filter="url(#soft-blur)">
        <ellipse cx="40" cy="60" rx="140" ry="110" fill="#a9d6e3" opacity="0.8"/>
        <ellipse cx="780" cy="70" rx="160" ry="120" fill="#a8c6de" opacity="0.75"/>
        <ellipse cx="740" cy="330" rx="170" ry="200" fill="#b3cde0" opacity="0.7"/>
        <ellipse cx="60" cy="470" rx="110" ry="240" fill="#c4dbe8" opacity="0.75"/>
        <ellipse cx="40" cy="820" rx="130" ry="150" fill="#a8dde9" opacity="0.85"/>
        <ellipse cx="690" cy="760" rx="150" ry="170" fill="#9dbdd8" opacity="0.8"/>
        <ellipse cx="420" cy="1130" rx="420" ry="110" fill="#b4cfe2" opacity="0.75"/>
        <ellipse cx="780" cy="1100" rx="140" ry="150" fill="#9fbfd8" opacity="0.8"/>
        <ellipse cx="330" cy="450" rx="220" ry="180" fill="#f3f5f8" opacity="0.85"/>
        <ellipse cx="420" cy="820" rx="180" ry="90" fill="#eef1f5" opacity="0.8"/>
      </g>
      <g filter="url(#soft-blur)" opacity="0.55">
        <path d="M-40 120 C 120 320, 200 620, 160 1000 L 230 1000 C 280 620, 200 300, 40 100 Z" fill="#ffffff"/>
        <path d="M560 180 C 680 300, 820 320, 900 260 L 900 360 C 800 420, 660 390, 540 260 Z" fill="#ffffff"/>
      </g>
      <rect width="846" height="1200" filter="url(#grain)" opacity="0.35"/>
    </svg>

    <header class="author-band">
      <p class="author">DR. MIRA KESSOW</p>
    </header>

    <h1 class="title">
      <span class="title-line title-line--first">Morgenlicht</span>
      <span class="title-script">neu</span>
      <span class="title-line title-line--last">Entdecken</span>
    </h1>

    <svg class="wave" viewBox="0 0 846 100" aria-hidden="true">
      <path d="M0 86 C 120 20, 200 -5, 330 22 C 430 44, 520 90, 620 92 C 720 94, 780 60, 846 30"
            fill="none" stroke="#ffffff" stroke-width="3.2" stroke-linecap="round" stroke-dasharray="0.1 7"/>
    </svg>

    <section class="subtitle-band">
      <p class="subtitle">
        <span class="subtitle-line subtitle-line--first">Spüre den <span class="subtitle-script">Mut</span></span>
        <span class="subtitle-line subtitle-line--second">der ganz in dir wohnt!</span>
      </p>
    </section>
  </main>
</body>
</html>
```